Business Card Design Project

We need a new fresh business card for our business. There are multiple services we offer and we need a fresh corporate card that represents us better. We start from cleaning carpet and tiles, to upholstery and curtains, to completely clean all contents and building materials after a fire, or completely dry out a home or business after a major or minor flood event. We are open to all concepts as we want to create a new look, maybe even logo, signage, vehicle signage, uniforms.
We are open to new colours etc.

Go to www.brolvaquincare.com.au for current logo and all other past ideas

Target Market(s)

Everyone is our possible client but we are targeting more coorporate

Industry/Entity Type

Building

```html
<!DOCTYPE html>
<html lang="en">
<head>
<meta charset="utf-8">
<title>Brolvaquin Care – Business Card</title>
<link rel="stylesheet" href="https://fonts.googleapis.com/css2?family=Open+Sans:wght@400;600&family=Saira:wght@500&display=swap">
<style>
  :root {
    --backdrop: #e6e8eb;
    --card-white: #ffffff;
    --brand-blue: #1a5ea6;
    --brand-pink: #e0197d;
    --ink-dark: #2f3438;
    --text-light: #ffffff;
  }
  * { margin: 0; padding: 0; box-sizing: border-box; }
  html, body {
    width: 1200px; height: 901px; overflow: hidden;
    background: var(--backdrop);
  }
  .canvas {
    position: relative; width: 1200px; height: 901px;
    display: flex; align-items: center; justify-content: center;
  }
  .card {
    position: relative; width: 900px; height: 520px;
    background: var(--card-white);
    border-radius: 44px; overflow: hidden;
    box-shadow: 0 10px 30px rgba(0,0,0,0.15);
  }
  .card__swoosh { position: absolute; inset: 0; width: 100%; height: 100%; }
  .brand {
    position: absolute; left: 62px; top: 62px;
    display: flex; align-items: center; gap: 16px;
  }
  .brand__name {
    font-family: "Open Sans", sans-serif; font-weight: 600;
    font-size: 40px; color: var(--brand-blue); letter-spacing: 0.5px;
  }
  .brand__dot {
    width: 56px; height: 56px; border-radius: 50%;
    background: var(--brand-pink);
  }
  .person { position: absolute; left: 62px; top: 158px; }
  .person__name {
    font-family: "Saira", sans-serif; font-weight: 500;
    font-size: 30px; letter-spacing: 2px; color: var(--brand-blue);
  }
  .person__role {
    font-family: "Open Sans", sans-serif; font-size: 19px;
    color: var(--ink-dark); margin-top: 2px;
  }
  .contact {
    position: absolute; right: 40px; bottom: 34px;
    list-style: none; text-align: right;
    font-family: "Open Sans", sans-serif; font-size: 19px;
    color: var(--text-light); line-height: 30px;
  }
  .contact__item { display: flex; justify-content: flex-end; align-items: center; gap: 12px; }
  .contact__icon { width: 20px; height: 20px; flex: none; }
</style>
</head>
<body>
<main class="canvas">
  <article class="card">
    <svg class="card__swoosh" viewBox="0 0 900 520" preserveAspectRatio="none" aria-hidden="true">
      <path d="M0,238 C240,360 470,350 900,170 L900,520 L0,520 Z" fill="var(--brand-blue)"/>
      <path d="M0,212 C230,318 420,330 640,262 C430,316 230,320 0,232 Z" fill="var(--brand-pink)"/>
    </svg>

    <div class="brand">
      <span class="brand__name">Brolvaquin Care</span>
      <span class="brand__dot"></span>
    </div>

    <div class="person">
      <h1 class="person__name">MARCUS DELANEY</h1>
      <p class="person__role">Managing Director</p>
    </div>

    <ul class="contact">
      <li class="contact__item">012 345 6789
        <svg class="contact__icon" viewBox="0 0 20 20"><rect x="5" y="1.5" width="10" height="17" rx="2" fill="none" stroke="#fff" stroke-width="1.6"/><circle cx="10" cy="15.5" r="1" fill="#fff"/></svg>
      </li>
      <li class="contact__item">012 345 6789
        <svg class="contact__icon" viewBox="0 0 20 20"><path d="M5 2 L8 2 L9.5 6 L7.5 7.5 C8.5 10 10 11.5 12.5 12.5 L14 10.5 L18 12 L18 15 C18 16.5 17 17.5 15.5 17.5 C8.5 17 3 11.5 2.5 4.5 C2.5 3 3.5 2 5 2 Z" fill="#fff"/></svg>
      </li>
      <li class="contact__item">urname@email.com
        <svg class="contact__icon" viewBox="0 0 20 20"><rect x="1.5" y="4" width="17" height="12" fill="#fff"/><path d="M1.5 4 L10 11 L18.5 4" fill="none" stroke="var(--brand-blue)" stroke-width="1.4"/></svg>
      </li>
      <li class="contact__item">www.brolvaquincare.com.au
        <svg class="contact__icon" viewBox="0 0 20 20"><circle cx="10" cy="10" r="8" fill="none" stroke="#fff" stroke-width="1.6"/><ellipse cx="10" cy="10" rx="3.5" ry="8" fill="none" stroke="#fff" stroke-width="1.4"/><path d="M2 10 H18 M3.5 6 H16.5 M3.5 14 H16.5" stroke="#fff" stroke-width="1.2"/></svg>
      </li>
      <li class="contact__item">045.12th floor,Harbour Line Road QLD
        <svg class="contact__icon" viewBox="0 0 20 20"><path d="M10 1.5 C6.5 1.5 4 4 4 7.5 C4 12 10 18.5 10 18.5 C10 18.5 16 12 16 7.5 C16 4 13.5 1.5 10 1.5 Z" fill="#fff"/><circle cx="10" cy="7.5" r="2.3" fill="var(--brand-blue)"/></svg>
      </li>
    </ul>
  </article>
</main>
</body>
</html>
```